I need a letterhead for a newsletter that will go out quarterly to the dentists of the 18th district. It is called "The Crestline Digest" We are in Amarillo TX and have this landmark in the photo as our most prominent feature. If it could be used, that would be cool.
This is a professional organization newsletter so the letterhead should be somewhat professional.

Target Market(s)

Dentists

Industry/Entity Type

Dental

Font styles to use
Serif

Colors

Designer to choose only greyscale colors for use in the design.

Requirements
Must have
• I want the title of "The Crestline Digest" to be the on top with the phrase "Cobalt Ridge Dental Society" written underneath.
Nice to have
• the photo incorporated could be incorporated in black and white or color along the bottom of the letterhead or with the title inside the photo.
Should not have
• I don't want it to be cartoony. I want it to be stylish and elegant and professional.

```html
<!DOCTYPE html>
<html lang="en">
<head>
<meta charset="utf-8">
<title>The Crestline Digest — Newsletter Letterhead</title>
<link href="https://fonts.googleapis.com/css2?family=Libre+Baskerville:ital,wght@0,400;0,700;1,400&display=swap" rel="stylesheet">
<style>
  :root {
    --backdrop: #e4e4e4;
    --paper: #ffffff;
    --ink: #1e1e1e;
    --ink-soft: #5a5a5a;
    --band: #3a3a3a;
    --band-text: #ffffff;
    --rule: #bdbdbd;
    --mark: #6e6e6e;
  }
  * { margin: 0; padding: 0; box-sizing: border-box; }
  html, body {
    width: 1200px;
    height: 898px;
    overflow: hidden;
    background: var(--backdrop);
    font-family: "Libre Baskerville", Georgia, serif;
  }
  .letterhead {
    position: absolute;
    left: 310px;
    top: 39px;
    width: 580px;
    height: 820px;
    background: var(--paper);
    box-shadow: 0 6px 24px rgba(0, 0, 0, 0.14);
  }
  .masthead {
    position: absolute;
    left: 32px;
    right: 32px;
    top: 34px;
    text-align: center;
  }
  .masthead .title {
    font-size: 32px;
    font-weight: 700;
    color: var(--ink);
    letter-spacing: 0.5px;
    line-height: 1.2;
  }
  .masthead .society {
    margin-top: 8px;
    font-size: 13px;
    font-style: italic;
    color: var(--ink-soft);
    letter-spacing: 1px;
  }
  .issue-band {
    position: absolute;
    left: 32px;
    right: 32px;
    top: 132px;
    height: 40px;
    background: var(--band);
    color: var(--band-text);
    display: flex;
    align-items: center;
    justify-content: space-between;
    padding: 0 22px;
    font-size: 14px;
    letter-spacing: 0.4px;
  }
  .footer-rule {
    position: absolute;
    left: 32px;
    right: 32px;
    bottom: 84px;
    height: 1px;
    background: var(--rule);
  }
  .society-mark {
    position: absolute;
    left: 32px;
    bottom: 34px;
    display: flex;
    align-items: center;
    gap: 10px;
    color: var(--mark);
    font-size: 12px;
  }
  .society-mark .dot {
    width: 34px;
    height: 34px;
    border-radius: 50%;
    background: var(--mark);
    flex: none;
  }
</style>
</head>
<body>
  <main class="letterhead">
    <header class="masthead">
      <h1 class="title">The Crestline Digest</h1>
      <p class="society">Cobalt Ridge Dental Society</p>
    </header>
    <div class="issue-band">
      <span class="label">Newsletter</span>
      <span class="date">Oct 2019</span>
      <span class="issue">Issue no 001</span>
    </div>
    <div class="footer-rule" aria-hidden="true"></div>
    <footer class="society-mark">
      <span class="dot" aria-hidden="true"></span>
      <span class="society-name">Cobalt Ridge Dental Society</span>
    </footer>
  </main>
</body>
</html>
```